Company director needs a business card design

I am a semi-retired former senior finance executive who sits on a number of public and private company boards and do some consulting work. I work largely with emerging businesses but deal regularly with top end of town lawyers, bankers etc. I need a thoughtful but relatively conservative design which would also resonate with my younger client base. Some colour would be good. Information limited to name, address, office tel, mobile and email.

Finance

```html
<!DOCTYPE html>
<html lang="en">
<head>
<meta charset="utf-8">
<title>Martin Caldwell – Business Card</title>
<link rel="stylesheet" href="https://fonts.googleapis.com/css2?family=Arimo:wght@400;700&family=Tulpen+One&display=swap">
<style>
  :root {
    --page-bg: #f1f1f1;
    --card-grey: #808080;
    --card-white: #ffffff;
    --ink-dark: #4a4a4a;
    --ink-name-back: #555555;
    --ink-name-front: #808080;
    --ink-contact: #3d3d3d;
    --accent-bar: #808080;
  }
  * { margin: 0; padding: 0; box-sizing: border-box; }
  html, body { width: 1200px; height: 900px; overflow: hidden; }
  body {
    position: relative;
    background: var(--page-bg);
    font-family: "Arimo", Arial, sans-serif;
  }
  .card {
    position: absolute;
    box-shadow: 0 12px 24px rgba(0,0,0,0.35);
  }
  .card--back { left: 288px; top: 72px; width: 621px; height: 353px; background: var(--card-grey); }
  .card--front { left: 288px; top: 476px; width: 618px; height: 353px; background: var(--card-white); }

  .contact-item {
    position: absolute;
    display: flex;
    align-items: center;
    font-size: 14px;
    white-space: nowrap;
  }
  .contact-item svg { width: 18px; height: 18px; margin-right: 6px; flex: none; }
  .contact-item--strong { font-weight: 700; }
  .card--back .contact-item { color: var(--ink-dark); left: 14px; }
  .card--back .contact-item svg { stroke: var(--ink-dark); }
  .card--front .contact-item { color: var(--ink-contact); }
  .card--front .contact-item svg { stroke: var(--ink-contact); }

  .name {
    position: absolute;
    font-family: "Tulpen One", "Arial Narrow", sans-serif;
    font-size: 46px;
    letter-spacing: 3px;
    text-transform: uppercase;
    line-height: 1;
    white-space: nowrap;
  }
  .card--back .name { left: 0; right: 0; top: 176px; text-align: center; color: var(--ink-name-back); padding-left: 28px; }
  .card--front .name { left: 28px; top: 164px; color: var(--ink-name-front); }

  .accent-bar {
    position: absolute;
    left: 296px; top: 166px;
    width: 13px; height: 164px;
    background: var(--accent-bar);
  }
  svg .icon { fill: none; stroke-width: 1.4; stroke-linecap: round; stroke-linejoin: round; }
</style>
</head>
<body>

<svg width="0" height="0" style="position:absolute">
  <defs>
    <symbol id="icon-mobile" viewBox="0 0 18 18"><g class="icon"><rect x="5" y="1" width="8" height="16" rx="1"/><line x1="5" y1="13.5" x2="13" y2="13.5"/><circle cx="9" cy="15.3" r="0.4"/></g></symbol>
    <symbol id="icon-phone" viewBox="0 0 18 18"><g class="icon"><path d="M4 2l3 3-1.6 2.2c1 2 2.6 3.6 4.6 4.6L12.2 10l3 3-2 2.2C8 15 3 10 2 4.2z"/></g></symbol>
    <symbol id="icon-mail" viewBox="0 0 18 18"><g class="icon"><rect x="1" y="4" width="16" height="10"/><path d="M1 4l8 6 8-6"/></g></symbol>
    <symbol id="icon-pin" viewBox="0 0 18 18"><g class="icon"><path d="M9 17s-5-6-5-10a5 5 0 0 1 10 0c0 4-5 10-5 10z"/><circle cx="9" cy="7" r="1.8"/></g></symbol>
  </defs>
</svg>

<section class="card card--back" aria-label="Card back">
  <div class="contact-item contact-item--strong" style="top:11px"><svg><use href="#icon-mobile"/></svg>+ 61 400 555 218</div>
  <div class="contact-item contact-item--strong" style="top:35px"><svg><use href="#icon-phone"/></svg>+ 61 2 9000 4821</div>
  <div class="contact-item contact-item--strong" style="top:58px"><svg><use href="#icon-mail"/></svg>martin_caldwell@corvus.net.au</div>
  <div class="contact-item" style="top:88px"><svg><use href="#icon-pin"/></svg>18 Banksia Parade, Harbourside NSW 2090</div>
  <h1 class="name">Martin Caldwell</h1>
</section>

<section class="card card--front" aria-label="Card front">
  <h2 class="name">Martin Caldwell</h2>
  <div class="accent-bar"></div>
  <div class="contact-item contact-item--strong" style="left:318px; top:224px"><svg><use href="#icon-mobile"/></svg>+ 61 400 555 218</div>
  <div class="contact-item contact-item--strong" style="left:318px; top:254px"><svg><use href="#icon-phone"/></svg>+61 2 9000 4821</div>
  <div class="contact-item contact-item--strong" style="left:318px; top:282px"><svg><use href="#icon-mail"/></svg>martin_caldwell@corvus.net.au</div>
  <div class="contact-item" style="left:318px; top:314px"><svg><use href="#icon-pin"/></svg>18 Banksia Parade, Harbourside NSW 2090</div>
</section>

</body>
</html>
```